Food and Beverage Business Cards

We need business cards with logo designs for a consultant in the food and beverage industry. We specialize in helping restaurants fix operational and management problems.
Specific areas of expertise include:
-Steps of service
-Staff management tools
-Standard operating procedures
-Profit and loss management
-Inventory
-Point of sales
-Bar Menu
-Mystery shopper service
-Handling and managing suppliers

Target Market(s)

Restaurant and bar owners and managers

Industry/Entity Type

Business

Contact Information for Business Card

Mathieu Girardot
Q&T Consulting
phone: 15027390614
mathqt@sampleinbox.com

Font styles to use
Other font styles liked:
• Check out the screen shot font idea

Colors

Designer to choose colors to be used in the design.

Requirements
Must have
• Must include QR code (See attachment)
• Logo should reflect our specific focus on the drinks side of the industry.
• Areas of Expertise:
• -Service Steps
• -Staff management tools
• -S.O.P
• -P&L Management
• -Inventory
• -P.O.S
• -Bar Menu
• -Mystery Shopper Service
• -Handling and Managing Suppliers

```html
<!DOCTYPE html>
<html lang="en">
<head>
<meta charset="utf-8">
<title>Q&amp;T Consulting Business Cards</title>
<link href="https://fonts.googleapis.com/css2?family=PT+Serif:wght@400;700&family=Roboto:wght@400;700&display=swap" rel="stylesheet">
<style>
  :root {
    --page: #e9e7e4;
    --card-white: #f6f6f5;
    --card-black: #141414;
    --band-grey: #666666;
    --band-dark: #2a2a2a;
    --ink: #1b1b1b;
    --ink-soft: #5a5a5a;
    --paper-text: #f2f2f2;
    --badge: #d9d9d9;
  }
  * { margin: 0; padding: 0; box-sizing: border-box; }
  html, body { width: 1200px; height: 886px; overflow: hidden; }
  body {
    background: var(--page);
    font-family: "PT Serif", Georgia, serif;
    display: flex; flex-direction: column; align-items: center; justify-content: center;
    gap: 46px;
  }
  .card {
    width: 560px; height: 320px; position: relative; overflow: hidden;
    box-shadow: 0 6px 18px rgba(0,0,0,.18);
  }

  /* Brand name */
  .brand-name {
    display: flex; align-items: center; gap: 12px;
    font-size: 34px; font-weight: 400; line-height: 1; white-space: nowrap;
  }
  .brand-square { width: 16px; height: 16px; background: currentColor; flex: none; }

  /* Front */
  .card-front { background: var(--card-white); }
  .card-front .brand-name {
    position: absolute; left: 0; width: 58%; top: 92px; justify-content: center; color: var(--ink);
  }
  .info-band { position: absolute; left: 0; right: 0; top: 192px; height: 58px; display: flex; }
  .identity {
    flex: 0 0 58%; background: var(--band-grey); color: var(--paper-text);
    display: flex; flex-direction: column; justify-content: center; align-items: flex-end;
    padding-right: 22px; line-height: 1.2;
  }
  .identity .person { font-size: 17px; }
  .identity .company { font-size: 14px; }
  .contact {
    flex: 1; background: var(--band-dark); color: var(--paper-text);
    display: flex; flex-direction: column; justify-content: center; gap: 5px;
    padding-left: 16px; font-size: 12.5px; white-space: nowrap;
  }
  .contact-line { display: flex; align-items: center; gap: 8px; }
  .contact-line svg { width: 12px; height: 12px; fill: var(--paper-text); flex: none; }
  .website {
    position: absolute; left: 58%; right: 0; top: 272px; text-align: center;
    font-size: 12px; letter-spacing: 4px; color: var(--ink-soft); white-space: nowrap;
  }

  /* Back */
  .card-back { background: var(--card-black); color: var(--paper-text); }
  .expertise {
    position: absolute; left: 34px; top: 40px; width: 250px;
    font-family: "Roboto", Arial, sans-serif; font-size: 12.5px; line-height: 1.55;
  }
  .expertise h2 { font-size: 16px; font-weight: 700; margin-bottom: 8px; }
  .card-back .brand-name {
    position: absolute; right: 30px; top: 120px; color: var(--paper-text); font-size: 30px;
  }
  .badges { position: absolute; right: 22px; bottom: 20px; display: flex; gap: 10px; }
  .badge { width: 40px; height: 40px; border-radius: 50%; background: var(--badge); }
</style>
</head>
<body>
  <section class="card card-front">
    <div class="brand-name"><span class="brand-square"></span><span>Quayside Taps</span></div>
    <div class="info-band">
      <div class="identity">
        <span class="person">Mathieu Girardot</span>
        <span class="company">Q&amp;T Consulting</span>
      </div>
      <div class="contact">
        <div class="contact-line">
          <svg viewBox="0 0 24 24"><path d="M6.6 10.8a15.1 15.1 0 0 0 6.6 6.6l2.2-2.2a1 1 0 0 1 1-.25 11.4 11.4 0 0 0 3.6.57 1 1 0 0 1 1 1V20a1 1 0 0 1-1 1A17 17 0 0 1 3 4a1 1 0 0 1 1-1h3.5a1 1 0 0 1 1 1c0 1.25.2 2.450.57 3.57a1 1 0 0 1-.25 1z"/></svg>
          <span>15027390614</span>
        </div>
        <div class="contact-line">
          <svg viewBox="0 0 24 24"><path d="M2 5h20v14H2z M4 7v.5l8 5 8-5V7l-8 5z" fill-rule="evenodd"/></svg>
          <span>mathqt@sampleinbox.com</span>
        </div>
      </div>
    </div>
    <div class="website">www.quaysidetaps.com</div>
  </section>

  <section class="card card-back">
    <div class="expertise">
      <h2>Areas of Expertise</h2>
      <p>Service Steps | Staff Management Tools | S.O.P | P&amp;L Management | Inventory | P.O.S | Bar Menu | Mystery Shopper Service | Handling and Managing Suppliers</p>
    </div>
    <div class="brand-name"><span class="brand-square"></span><span>Quayside Taps</span></div>
    <div class="badges">
      <div class="badge"></div>
      <div class="badge"></div>
    </div>
  </section>
</body>
</html>
```